Flyer-Design für Ofenservice Firma
Zielgruppe
Die Firma hat als Kerngeschäft Wartung, Reinigung, Reparatur und Inbetriebnahme von Öfen und Kaminen aller Art. Der Fokus liegt dabei auf Pelletöfen. Die Firma versteht sich als zuverlässiger Dienstleister mit gutem Preisleistungsverhältnis. Zielgruppe sind hauptsächlich private Bewohner von Einfamilienhäusern in der ländlichen Gegend (Hessen)
Aufgabenstellung
Zur Bekanntmachung nach Neugründung soll ein Faltflyer gestaltet werden mit insgesamt 6 Bereichen. Die Informationen, welche auf den Flyer sollen, entnehmen Sie bitte dem Entwurf (flyer.pdf). Dieser stellt nur eine erste Idee dar und darf gerne nach Belieben verändert bzw. neu gestaltet werden. Die enthaltenen Informationen, sollten im Großen und Ganzen aber beibehalten werden. Schön wäre evtl. auch eine Hervorhebung der Preise, da wir Preisführer im Markt sind. Auch die Bilder unseres Teams sollen in den Flyer integriert sein. Auf Anfrage kann ich auch gerne weitere Kamin- und Ofenfotos zur Verfügung stellen, für welche ich die Nutzungsrechte habe. Falls Sie weitere Informationen benötigen oder Fragen haben, kommen Sie gerne auf mich zu. Die Bilder dürfen gerne etwas ausgeschnitten werden. Es geht in erster Linie darum, dass die Kunden erkennen, welche Art von Ofen sie zu Hause haben.

```html
<!DOCTYPE html>
<html lang="de">
<head>
<meta charset="utf-8">
<title>KALORIS Ofenservice – Faltflyer Innenseite</title>
<link rel="stylesheet" href="https://fonts.googleapis.com/css2?family=Open+Sans:wght@300;400;600;700;800&display=swap">
<style>
  :root {
    --slate: #4a5a63;
    --slate-dark: #3c4a52;
    --orange: #e07b2e;
    --orange-box: #df7f36;
    --ink: #4a4f54;
    --paper: #ffffff;
    --stage: #e4e5e7;
    --photo-a: #c9d1d6;
    --photo-b: #8d9aa3;
  }
  * { box-sizing: border-box; margin: 0; padding: 0; }
  html, body { width: 1200px; height: 900px; overflow: hidden; }
  body {
    background: var(--stage);
    font-family: "Open Sans", Arial, sans-serif;
    color: var(--ink);
    display: flex; align-items: center; justify-content: center;
  }
  .spread { display: flex; width: 840px; height: 860px; box-shadow: 0 10px 30px rgba(0,0,0,.15); }
  .panel { position: relative; width: 420px; height: 100%; overflow: hidden; }

  /* left panel */
  .panel--pellets { background: var(--slate); color: #fff; }
  .pellets__text { padding: 48px 36px 0 40px; }
  .pellets__kicker { font-size: 40px; font-weight: 300; line-height: 1; color: rgba(255,255,255,.55); }
  .pellets__title { font-size: 44px; font-weight: 800; line-height: 1.05; margin-bottom: 26px; }
  .pellets__lead { font-size: 14px; font-weight: 700; margin-bottom: 10px; }
  .service-list { list-style: none; font-size: 14px; line-height: 1.45; }
  .service-list li { position: relative; padding-left: 16px; margin-bottom: 5px; }
  .service-list li::before { content: "•"; position: absolute; left: 0; }
  .pellets__photo {
    position: absolute; left: 0; right: 0; bottom: 0; height: 360px;
    background: linear-gradient(160deg, #b7c7d3 0%, #d8d2c6 45%, #9aa6ae 100%);
    clip-path: polygon(0 18%, 100% 0, 100% 100%, 0 100%);
  }
  .price-box {
    position: absolute; left: 26px; right: 26px; bottom: 70px;
    background: rgba(255,255,255,.82); color: var(--ink);
    padding: 16px 20px; font-size: 15px; line-height: 1.5;
  }
  .price-box__label { font-weight: 700; }
  .price-box__main { color: var(--orange); font-weight: 600; }
  .price-box__alt { font-weight: 600; }

  /* right panel */
  .panel--service { background: var(--paper); }
  .service__intro { padding: 56px 36px 0 36px; }
  .service__headline { font-size: 19px; line-height: 1.25; font-weight: 400; color: var(--slate); margin-bottom: 18px; }
  .service__headline strong { color: var(--orange); font-weight: 700; }
  .brand-name { color: var(--slate-dark); font-weight: 700; }
  .service__body p { font-size: 12px; line-height: 1.5; text-align: justify; margin-bottom: 12px; }
  .service__body b { font-weight: 700; }
  .service__photo {
    position: absolute; left: 0; right: 0; bottom: 0; height: 440px;
    background: linear-gradient(180deg, #eceeef 0%, var(--photo-a) 40%, var(--photo-b) 100%);
  }
  .more-box {
    position: absolute; left: 24px; right: 28px; top: 470px;
    background: var(--orange-box); color: #fff;
    padding: 20px 24px 22px; font-size: 13px; line-height: 1.5;
  }
  .more-box__title { font-size: 16px; font-weight: 700; margin-bottom: 12px; }
  .more-box p { margin-bottom: 12px; }
  .more-box p:last-child { margin-bottom: 0; }
  .more-box b { font-weight: 700; }
</style>
</head>
<body>
  <main class="spread">
    <section class="panel panel--pellets">
      <div class="pellets__text">
        <p class="pellets__kicker">Die</p>
        <h1 class="pellets__title">Pelletöfen</h1>
        <p class="pellets__lead">Die Wartung beinhaltet:</p>
        <ul class="service-list">
          <li>Reinigung von Sichtscheibe, Brenntopf, Feuerraum, Zwischenboden, gesamter Feuerraum, sämtliche Rauchgaszüge und Aschebehälter</li>
          <li>Reinigung des Saugzuggebläses</li>
          <li>Überprüfung und Reinigung des Luftmengensensors</li>
          <li>Überprüfung der elektrischen Zündung</li>
          <li>Überprüfung der Dichtungen (Türdichtung, Türglasdichtung, Putzdeckeldichtungen)</li>
          <li>Überprüfung der Temperaturwächter</li>
          <li>Probelauf des Gerätes</li>
        </ul>
      </div>
      <div class="pellets__photo" role="img" aria-label="Foto: Wohnraum mit modernem Pelletofen und Flammen im Sichtfenster"></div>
      <div class="price-box">
        <p class="price-box__label">Preise:</p>
        <p class="price-box__main">Mit Wartungsvertrag: 140 € inkl. MwSt</p>
        <p class="price-box__alt">Ohne Wartungsvertrag: 180 € inkl. MwSt</p>
      </div>
    </section>

    <section class="panel panel--service">
      <div class="service__intro">
        <h2 class="service__headline"><strong>Der neue</strong> <span class="brand-name">KALORIS</span> Ofenservice<br>Noch mehr Service. Noch mehr Möglichkeiten.</h2>
        <div class="service__body">
          <p>Als Inhaber geführtes Unternehmen bieten wir <b>professionelle Serviceleistungen rund um Öfen aller Art</b> (Kaminöfen, Pelletöfen, Scheitholzöfen, Kachelöfen, offene Kamine, Grund- und Speicheröfen).</p>
          <p>Durch erfahrene Mitarbeiter, regelmäßigen Personalschulungen und <b>Zusammenarbeit mit namhaften Herstellern</b> können wir Ihnen eine breite Palette an Dienstleistungen rund um Kaminöfen bieten.</p>
          <p><b>Guter Service muss nicht teuer sein!</b> Überzeugen Sie sich von unserem <b>Preis-Leistungs-Verhältnis</b> sowie unseren <b>exklusiven Konditionen</b> bei Abschluss eines Wartungsvertrags.</p>
        </div>
      </div>
      <div class="service__photo" role="img" aria-label="Foto: moderner Kaminofen in hellem Wohnraum"></div>
      <div class="more-box">
        <h3 class="more-box__title">Weitere Leistungen:</h3>
        <p><b>Reparatur und Instandsetzung:</b> Funktioniert Ihr Ofen nicht richtig, sind wir schnellstmöglich für Sie da und setzen Ihren Ofen wieder instand.</p>
        <p><b>Inbetriebnahme:</b> Sie haben einen neuen Ofen erworben und möchten sich über die richtige Nutzung und Befeuerung informieren?</p>
        <p><b>Kaufberatung:</b> Sie planen eine Neuanschaffung und möchten sich vorab über Anschlussmöglichkeiten, Brennstoffarten und Modelle informieren? Wir beraten Sie unabhängig und auf Ihre Bedürfnisse zugeschnitten.</p>
      </div>
    </section>
  </main>
</body>
</html>
```